Yard sign

Looking for a yard sign. <br/>Something simple, name, number. <br/>Large text, readable from 50 feet away. <br/><br/>18 x 24 inches.

Target Market(s)

Potential homeowners thinking about going solar.

Colors

Designer to choose colors to be used in the design.

Requirements
Must have
• "WE'VE GONE SOLAR!"
Nice to have
• We are a solar company, we would like a design that compliments the homeowners decision that they went solar and encourages others to do the same.

```html
<!DOCTYPE html>
<html lang="en">
<head>
<meta charset="utf-8">
<title>Bright Ridge Solar – Yard Sign</title>
<link href="https://fonts.googleapis.com/css2?family=Montserrat:wght@700;800;900&family=Oswald:wght@500&display=swap" rel="stylesheet">
<style>
  :root{
    --backdrop:#231f20;
    --sign-dark:#2a2a2a;
    --sign-light:#444343;
    --sun-yellow:#fdc52c;
    --sun-orange:#f68b1f;
    --deep-orange:#db730c;
    --brand-orange:#f37709;
    --band-red:#dc450b;
    --headline-top:#fbb512;
    --headline-bottom:#e04e08;
    --white:#ffffff;
    --shadow:#0d0d0d;
  }
  *{margin:0;padding:0;box-sizing:border-box}
  html,body{width:1200px;height:1200px;overflow:hidden;background:var(--backdrop)}
  .yard-sign{
    position:absolute;left:47px;top:155px;width:1106px;height:829px;overflow:hidden;
    background:radial-gradient(ellipse at 50% 50%,var(--sign-light) 0%,var(--sign-dark) 55%,#1c1c1c 100%);
  }
  .top-swoosh{position:absolute;left:0;top:0;width:100%;height:100%}
  .brand{
    position:absolute;left:0;right:0;top:205px;
    display:flex;align-items:center;justify-content:center;gap:22px;
  }
  .brand-dot{width:74px;height:74px;border-radius:50%;background:var(--sun-yellow)}
  .brand-name{
    font-family:'Montserrat',sans-serif;font-weight:800;font-size:54px;
    color:var(--brand-orange);letter-spacing:1px;
  }
  .headline{
    position:absolute;left:0;right:0;top:412px;text-align:center;
    font-family:'Montserrat',sans-serif;font-weight:900;line-height:1;
  }
  .headline-line1{
    display:block;font-size:97px;color:var(--brand-orange);letter-spacing:1px;
    text-shadow:5px 5px 0 var(--shadow);
  }
  .headline-line2{
    display:inline-block;margin-top:6px;font-size:176px;letter-spacing:-2px;
    background:linear-gradient(to bottom,var(--headline-top) 0%,var(--headline-bottom) 85%);
    -webkit-background-clip:text;background-clip:text;color:transparent;
    filter:drop-shadow(5px 5px 0 var(--shadow));
  }
  .contact-band{
    position:absolute;left:0;right:0;top:689px;height:96px;background:var(--band-red);
    display:flex;align-items:center;justify-content:center;gap:22px;
    font-family:'Oswald',sans-serif;font-weight:500;font-size:84px;color:var(--white);
    letter-spacing:2px;
  }
  .contact-sep{width:26px;height:26px;border-radius:50%;background:var(--headline-top)}
</style>
</head>
<body>
  <div class="yard-sign">
    <svg class="top-swoosh" viewBox="0 0 1780 1334" preserveAspectRatio="none" aria-hidden="true">
      <path d="M0 0 H1780 V200 C1100 70 400 20 0 105 Z" fill="var(--sun-yellow)"/>
      <path d="M0 105 C400 20 1100 70 1780 200 V220 C1100 90 400 60 0 174 Z" fill="var(--sun-orange)"/>
      <path d="M1190 0 H1780 V120 C1580 70 1390 30 1190 0 Z" fill="var(--deep-orange)"/>
    </svg>

    <div class="brand">
      <span class="brand-dot"></span>
      <span class="brand-name">BRIGHT RIDGE SOLAR</span>
    </div>

    <h1 class="headline">
      <span class="headline-line1">WE'VE GONE</span>
      <span class="headline-line2">SOLAR!</span>
    </h1>

    <div class="contact-band">
      <span class="contact-name">DANIEL REYES</span>
      <span class="contact-sep"></span>
      <span class="contact-phone">555 014 2290</span>
    </div>
  </div>
</body>
</html>
```